skyPARLOR Helicopter Tour WordPress Website Design

SkyPARLOR (skyparlor-example.com) is a premium helicopter tour company offering scenic flights in two Florida cities: Tampa and Sarasota. We are seeking a full Wordpress website redesign that is modern, upbeat, inviting, and highly conversion‑focused. The new site should feel energetic and trustworthy, reflect the excitement of helicopter sightseeing, and maintain our recognizable SkyPARLOR color palette—while updating the overall look to feel fresh, clean, and current.
The website must be SEO‑friendly, mobile‑optimized, and easy to navigate. It should highlight our 5‑star customer reviews, showcase our tours clearly, and integrate seamlessly with TrailDock for instant online booking. The design should support a premium aviation experience while remaining friendly and accessible to tourists, families, couples, and adventure seekers.

These elements are essential and must be included in the design:

Brand & UX:
- Modern, upbeat, inviting design
- SEO‑friendly structure and layout
- Easy navigation and clear user flow
- Light grey “SP” background logo watermark (as used on current site)
- Clean, aviation‑inspired typography and layout

Conversion Features:
- Instant booking above the fold (TrailDock integration)
- Live Orbin Ratings carousel
- Tour comparison table (duration, route, price, etc.)
- FAQ expandable section
- Gift Cards page (highlighted as a major offering)
- What to Expect timeline (Arrive → Check‑In → Safety Briefing → Flight → Photos)
- Weather transparency widget (clear messaging about weather‑dependent flights

Content Structure:
- Separate pages for Tampa, Sarasota, and Gender Reveal Flights
- Pilot/Team profiles with short bios
- Highlighted features:
- Doors‑Off option
- Sunset flights
- Romantic packages
- Champagne add‑ons

Colors:
Use the existing SkyPARLOR palette as the foundation, but modernize it.
- Background: Clean with the light grey “SP” watermark integrated tastefully.
The overall color direction should feel bright, premium, energetic, and trustworthy

Target Market(s)

Tourists visiting Tampa or Sarasota, Families looking for memorable activities, Couples seeking romantic experiences (sunset flights, proposals, anniversaries), Adventure seekers and content creators, Locals celebrating birthdays, holidays, or special occasions, Gender reveal clients looking for a unique aerial reveal experience

Industry/Entity Type

Travel & Tourism / Aviation / Helicopter Tours / Experience‑based Activities

Requirements
Must have
• These elements are essential and must be included in the design: Brand & UX - Modern, upbeat, inviting design / SEO‑friendly structure and layout / Easy navigation and clear user flow / Light grey “SP” background logo watermark (as used on current site) / Clean, aviation‑inspired typography and layout
Nice to have
• Interactive route map showing flight paths / Subtle motion or parallax effects in hero sections / Animated icons or micro‑interactions / Social media integration (Instagram grid, TikTok clips) / Sticky mobile booking bar / Video header or short aerial footage loop / Subtle aviation‑themed graphic elements (rotor blur, sky gradients, etc.
Should not have
• No dark, heavy, or overly moody themes / No outdated fonts or overly playful typography / No cluttered layouts or excessive text blocks / No stocky, generic tourism imagery / No slow‑loading animations or heavy effects that hurt SEO

```html
<!DOCTYPE html>
<html lang="en">
<head>
<meta charset="utf-8">
<title>Gift Cards &amp; Safety</title>
<link href="https://fonts.googleapis.com/css2?family=Poppins:wght@700;800&family=Roboto:wght@400;500&display=swap" rel="stylesheet">
<style>
:root{
  --pink:#e83e8c;
  --blue:#0d6efd;
  --teal:#17a2b8;
  --green:#28a745;
  --gold:#ffc107;
  --ink:#2b2f36;
  --muted:#606a78;
  --sky:#d3e5fd;
  --white:#ffffff;
  --line:#d9dde3;
}
*{box-sizing:border-box;margin:0;padding:0}
html,body{width:927px;height:1200px;overflow:hidden;background:var(--white);font-family:'Roboto',sans-serif;color:var(--ink)}
.page{position:relative;width:927px;height:1200px;overflow:hidden}
.abs{position:absolute}
.pill{position:absolute;display:flex;align-items:center;gap:5px;padding:0 10px;height:24px;border-radius:12px;color:var(--white);font-size:9px;font-weight:500}
.display{font-family:'Poppins',sans-serif;font-weight:700;color:var(--ink);letter-spacing:-0.2px}
.lead{font-size:13px;line-height:21.6px;color:var(--muted)}

/* gift section */
.gift{left:7px;top:15px;width:913px;height:470px;background:linear-gradient(180deg,var(--sky) 0%,#e6f0fd 60%,#ffffff 100%)}
.gift-title{left:57px;top:101px;font-size:32.5px;line-height:44px}
.gift-copy{left:57px;top:156px;width:400px}
.perk{position:absolute;left:57px;display:flex;gap:11px;align-items:center}
.perk-icon{width:32px;height:32px;border-radius:50%;display:flex;align-items:center;justify-content:center;flex:none}
.perk-title{font-size:11px;font-weight:500;color:var(--ink);margin-bottom:6px}
.perk-text{font-size:10.7px;color:var(--muted)}
.btn{position:absolute;display:flex;align-items:center;justify-content:center;gap:6px;font-size:12px;font-weight:500;border-radius:4px}
.btn-pink{left:57px;top:391px;width:164px;height:42px;background:var(--pink);color:var(--white);box-shadow:0 6px 12px rgba(232,62,140,.25)}
.btn-outline{left:232px;top:391px;width:153px;height:42px;background:var(--white);border:1.5px solid var(--line);color:var(--ink)}

.collage{left:481px;top:121px;width:389px;height:287px}
.tile{position:absolute;width:144px;height:96px}
.float-card{position:absolute;background:var(--white);border-radius:6px;box-shadow:0 6px 18px rgba(30,50,90,.15);display:flex;align-items:center;gap:8px;padding:0 10px}
.float-title{font-size:8.5px;font-weight:500;color:var(--ink)}
.float-sub{font-size:7px;color:var(--muted);margin-top:2px}

/* safety section */
.safety-photo{left:57px;top:662px;width:390px;height:255px;border-radius:8px;background:linear-gradient(180deg,#8ccfe0 0%,#b9d9df 45%,#c4c7cb 80%,#d8b8a8 100%)}
.faa-card{left:103px;top:860px;width:299px;height:73px;background:var(--white);border-radius:4px;box-shadow:0 10px 24px rgba(30,50,90,.15);display:flex;align-items:center;justify-content:center;gap:12px}
.safety-title{left:480px;top:578px;font-size:32.5px;line-height:31px}
.safety-copy{left:480px;top:660px;width:375px}
.weather-box{left:480px;top:720px;width:390px;height:139px;background:var(--sky);border-radius:10px;padding:16px 16px}
.weather-head{display:flex;align-items:center;gap:6px;font-size:13px;font-weight:500;color:var(--ink)}
.weather-text{margin-top:13px;width:345px;font-size:10.3px;line-height:16px;color:var(--muted)}
.weather-points{display:flex;margin-top:14px}
.wp{width:184px;display:flex;gap:7px}
.wp-title{font-size:10.5px;font-weight:500}
.wp-sub{font-size:8.5px;color:var(--muted);margin-top:3px}
.checks{left:480px;top:881px;list-style:none}
.checks li{display:flex;align-items:center;gap:8px;font-size:10.7px;color:var(--muted);height:24px}
.btn-blue{left:480px;top:1001px;width:140px;height:40px;background:var(--blue);color:var(--white);box-shadow:0 6px 12px rgba(13,110,253,.2)}

/* faq */
.faq{left:7px;top:1094px;width:913px;height:106px;background:var(--sky);text-align:center}
.faq-title{margin-top:50px;font-size:32.5px;line-height:40px}
.faq-sub{margin-top:4px;font-size:12px;color:var(--muted)}
</style>
</head>
<body>
<div class="page">

  <section class="abs gift" aria-label="Gift cards"></section>

  <div class="pill" style="left:57px;top:68px;background:var(--pink)">
    <svg width="9" height="9" viewBox="0 0 10 10"><rect x="1" y="4" width="8" height="5" fill="#fff"/><rect x="0.5" y="2.5" width="9" height="2" fill="#fff"/><rect x="4.4" y="2.5" width="1.2" height="6.5" fill="var(--pink)"/></svg>
    Perfect for Any Occasion
  </div>
  <h1 class="abs display gift-title">Give the Gift of Flight</h1>
  <p class="abs lead gift-copy">Surprise your loved ones with an unforgettable helicopter tour experience. Our gift cards are perfect for birthdays, anniversaries, holidays, or any special celebration.</p>

  <div class="perk" style="top:238px">
    <div class="perk-icon" style="background:var(--blue)"><svg width="11" height="11" viewBox="0 0 10 10"><rect x="1" y="2" width="8" height="7" rx="1" fill="#fff"/><rect x="2.5" y="4.5" width="5" height="3" fill="var(--blue)"/></svg></div>
    <div><div class="perk-title">No Expiration Date</div><div class="perk-text">Gift cards never expire—book when it's convenient</div></div>
  </div>
  <div class="perk" style="top:284px">
    <div class="perk-icon" style="background:var(--green);color:#fff;font-size:12px;font-weight:500">$</div>
    <div><div class="perk-title">Flexible Amounts</div><div class="perk-text">Choose any dollar amount or specific tour package</div></div>
  </div>
  <div class="perk" style="top:329px">
    <div class="perk-icon" style="background:var(--teal)"><svg width="11" height="9" viewBox="0 0 10 8"><rect width="10" height="8" rx="1" fill="#fff"/><path d="M0.5 1 L5 4.5 L9.5 1" stroke="var(--teal)" fill="none"/></svg></div>
    <div><div class="perk-title">Instant Delivery</div><div class="perk-text">Digital gift cards delivered immediately via email</div></div>
  </div>

  <div class="btn btn-pink"><svg width="13" height="12" viewBox="0 0 12 11"><path d="M0 1h2l2 6h6l1.5-4.5H3" fill="#fff"/><circle cx="4.5" cy="9.5" r="1" fill="#fff"/><circle cx="9" cy="9.5" r="1" fill="#fff"/></svg>Purchase Gift Card</div>
  <div class="btn btn-outline"><svg width="12" height="12" viewBox="0 0 12 12"><circle cx="6" cy="6" r="6" fill="var(--ink)"/><text x="6" y="9" font-size="8" text-anchor="middle" fill="#fff" font-family="Roboto">?</text></svg>Have Questions?</div>

  <div class="abs collage">
    <div class="tile" role="img" aria-label="Couple smiling in helicopter cabin" style="left:0;top:0;background:linear-gradient(135deg,#a07050,#e6d8c8)"></div>
    <div class="tile" role="img" aria-label="Pilot flying over the bay" style="left:144px;top:0;background:linear-gradient(180deg,#6cc0d8,#2f7f8f)"></div>
    <div class="tile" role="img" aria-label="City lights seen from above at dusk" style="left:288px;top:0;width:101px;height:192px;background:linear-gradient(180deg,#3a4a58,#c0603a)"></div>
    <div class="tile" role="img" aria-label="Passenger posing beside helicopter on the pad" style="left:0;top:96px;background:linear-gradient(180deg,#8fd0e4,#a8a8a8)"></div>
    <div class="tile" role="img" aria-label="Passenger looking out over the city" style="left:144px;top:96px;background:linear-gradient(135deg,#c8d8e0,#8fa8b8)"></div>
    <div class="tile" role="img" aria-label="Couple toasting champagne on board" style="left:103px;top:192px;background:linear-gradient(135deg,#6a5040,#d6b08a)"></div>
    <div class="tile" role="img" aria-label="Pilot and guest in cockpit over the coast" style="left:247px;top:192px;width:142px;background:linear-gradient(135deg,#80b8cc,#304860)"></div>
    <div class="tile" style="left:0;top:192px;width:103px;height:30px;background:#a9c6ea"></div>
  </div>

  <div class="float-card" style="left:771px;top:104px;width:115px;height:53px">
    <svg width="32" height="32" viewBox="0 0 32 32"><circle cx="16" cy="16" r="16" fill="var(--gold)"/><path d="M16 8l2.4 5 5.4.7-4 3.8 1 5.4L16 20.3l-4.8 2.6 1-5.4-4-3.8 5.4-.7z" fill="var(--ink)"/></svg>
    <div><div class="float-title">5-Star Rated</div><div class="float-sub">500+ Reviews</div></div>
  </div>
  <div class="float-card" style="left:464px;top:342px;width:119px;height:54px">
    <svg width="32" height="32" viewBox="0 0 32 32"><circle cx="16" cy="16" r="16" fill="var(--green)"/><path d="M16 23l-6-6a3.5 3.5 0 0 1 6-4 3.5 3.5 0 0 1 6 4z" fill="#fff"/></svg>
    <div><div class="float-title">Most Gifted</div><div class="float-sub">Experience 2025</div></div>
  </div>

  <div class="abs safety-photo" role="img" aria-label="Passenger standing on the helipad in front of a helicopter"></div>
  <div class="abs faa-card">
    <svg width="42" height="42" viewBox="0 0 42 42"><circle cx="21" cy="21" r="21" fill="var(--green)"/><path d="M21 12l7 3v5c0 5-3 8-7 10-4-2-7-5-7-10v-5z" fill="#fff"/><path d="M21 15.5l4 1.7v3c0 3-1.7 5-4 6.3z" fill="var(--green)"/></svg>
    <div><div style="font-size:12px;font-weight:500">FAA Certified</div><div style="font-size:9.5px;color:var(--muted);margin-top:3px">Safety is our #1 priority</div></div>
  </div>

  <div class="pill" style="left:480px;top:540px;background:var(--teal)">
    <svg width="11" height="9" viewBox="0 0 12 9"><circle cx="4" cy="3.5" r="2.5" fill="#fff"/><rect x="2" y="4.5" width="9" height="4" rx="2" fill="#fff"/></svg>
    Weather &amp; Safety
  </div>
  <h2 class="abs display safety-title">Your Safety is Our<br>Priority</h2>
  <p class="abs lead safety-copy">We monitor weather conditions continuously to ensure optimal flying conditions. Your safety and comfort always come first.</p>

  <div class="abs weather-box">
    <div class="weather-head"><svg width="13" height="13" viewBox="0 0 12 12"><circle cx="6" cy="6" r="6" fill="var(--blue)"/><rect x="5.4" y="5" width="1.2" height="4" fill="#fff"/><circle cx="6" cy="3.3" r=".8" fill="#fff"/></svg>Weather-Dependent Flights</div>
    <p class="weather-text">Helicopter tours require good weather and visibility. If conditions aren't safe, we'll reschedule your flight at no extra charge.</p>
    <div class="weather-points">
      <div class="wp"><svg width="11" height="11" viewBox="0 0 12 12"><circle cx="6" cy="6" r="6" fill="var(--green)"/><path d="M3.3 6.2l1.8 1.8 3.6-3.7" stroke="#fff" stroke-width="1.4" fill="none"/></svg><div><div class="wp-title">Free Rescheduling</div><div class="wp-sub">No penalties for weather</div></div></div>
      <div class="wp"><svg width="11" height="11" viewBox="0 0 12 12"><circle cx="6" cy="6" r="6" fill="var(--green)"/><path d="M3.3 6.2l1.8 1.8 3.6-3.7" stroke="#fff" stroke-width="1.4" fill="none"/></svg><div><div class="wp-title">24/7 Updates</div><div class="wp-sub">Real-time notifications</div></div></div>
    </div>
  </div>

  <ul class="abs checks">
    <li><svg width="10" height="8" viewBox="0 0 10 8"><path d="M1 4l3 3 5-6" stroke="var(--green)" stroke-width="1.5" fill="none"/></svg>FAA-certified pilots with 1000+ flight hours</li>
    <li><svg width="10" height="8" viewBox="0 0 10 8"><path d="M1 4l3 3 5-6" stroke="var(--green)" stroke-width="1.5" fill="none"/></svg>Regularly maintained and inspected aircraft</li>
    <li><svg width="10" height="8" viewBox="0 0 10 8"><path d="M1 4l3 3 5-6" stroke="var(--green)" stroke-width="1.5" fill="none"/></svg>Comprehensive safety briefing before every flight</li>
    <li><svg width="10" height="8" viewBox="0 0 10 8"><path d="M1 4l3 3 5-6" stroke="var(--green)" stroke-width="1.5" fill="none"/></svg>Full insurance coverage for all passengers</li>
  </ul>

  <div class="btn btn-blue"><svg width="12" height="12" viewBox="0 0 12 12"><circle cx="6" cy="6" r="6" fill="#fff"/><text x="6" y="9" font-size="8" text-anchor="middle" fill="var(--blue)" font-family="Roboto">?</text></svg>Read Our FAQs</div>

  <section class="abs faq">
    <h2 class="display faq-title">Frequently Asked Questions</h2>
    <p class="faq-sub">Get answers to common questions about our helicopter tours</p>
  </section>

</div>
</body>
</html>
```